Web Design Project

We are an IT System Integrator. We provide Korvin 450 ERP System, CRM etc. We also provide hardware, networking servicing. Please look at www.zolvantix.com.sg. They provide the same service as us. We like to redesign our web site. I will attached the color that I prefer for reference.

Our website is www.tadurk.com.sg.  It has been created about 14 years ago.  We are trying to revamp it with a new look and information.   The new website must be informative, fast.    I have attached an attachment which show the color that I prefer(brownish golden).   

Our competitor (www.zolvantix.com) is carrying the same trade as us.  They have all the informations In their website that we will like to have.  Therefore I recommend you to take a look at my competitor website and have a better   
understanding on the kind of information I would like to have for my new website.

This project is guarantee to the person with the best design.  We can have it guarantee.

Target Market(s)

Corporate and companies

Industry/Entity Type

Hardware

```html
<!DOCTYPE html>
<html lang="en">
<head>
<meta charset="utf-8">
<title>Veltrane Information System</title>
<link rel="stylesheet" href="https://fonts.googleapis.com/css2?family=Roboto+Condensed:wght@400;700&family=PT+Sans:wght@400;700&display=swap">
<style>
:root{
  --bg-top:#9c6d37;
  --bg-bottom:#cf9f48;
  --page:#ececec;
  --band:#f6f6f6;
  --ink:#2b1c07;
  --body:#3c3326;
  --gold-link:#7d5410;
  --nav:#6c6458;
  --nav-active:#8e5a1b;
  --contact:#a4641a;
  --testi:#e0ad52;
  --quote:#3a2a0c;
  --news:#a35f16;
  --submit:#e0ad52;
  --logo-grey:#9a9a9a;
}
*{box-sizing:border-box;margin:0;padding:0}
html,body{width:912px;height:1200px;overflow:hidden}
body{
  position:relative;
  background:linear-gradient(180deg,var(--bg-top) 0,#b88a44 260px,var(--bg-bottom) 700px,var(--bg-bottom) 100%);
  font-family:"PT Sans",Arial,sans-serif;color:var(--body);
}
.page{
  position:absolute;left:76px;top:41px;width:760px;height:1070px;
  background:var(--page);border-top:2px dashed #d8d8d8;
  box-shadow:0 0 40px rgba(70,40,5,.45);
}
.page::after{
  content:"";position:absolute;left:170px;right:170px;bottom:-14px;height:14px;
  background:radial-gradient(ellipse at top,rgba(60,35,5,.55),rgba(60,35,5,0) 70%);
}
.abs{position:absolute}

/* header */
.brand{left:16px;top:30px;display:flex;align-items:center;gap:10px}
.brand-mark{width:52px;height:52px;border-radius:50%;background:radial-gradient(circle at 35% 35%,#e8c27a,#9c6a22)}
.brand-name{font-family:"Roboto Condensed",Arial,sans-serif;font-weight:700;font-size:13px;line-height:13px;color:#4a3416;width:80px}
.nav{right:26px;top:44px;display:flex;gap:20px;font-family:"Roboto Condensed",Arial,sans-serif;font-size:14px}
.nav a{color:var(--nav);text-decoration:none;padding:3px 8px;line-height:18px}
.nav a.active{background:var(--nav-active);color:#fff}

/* hero */
.hero{left:10px;top:99px;width:739px;height:292px;overflow:hidden;
  background:radial-gradient(ellipse 260px 200px at 560px 130px,#fff3c8 0,#e2b15a 35%,rgba(180,120,40,0) 75%),
  linear-gradient(90deg,#b97a22 0,#d49b44 45%,#a56c22 100%)}
.hero-art{position:absolute;right:0;top:0;width:380px;height:292px;
  background:radial-gradient(ellipse 150px 90px at 150px 150px,rgba(40,20,0,.55),rgba(40,20,0,0) 80%)}
.hero-caption{position:absolute;left:0;top:91px;width:303px;height:123px;background:rgba(160,90,20,.72);padding:10px 18px}
.hero-caption h1{font-family:"Roboto Condensed",Arial,sans-serif;font-weight:700;font-size:29px;line-height:25px;color:#fff}
.hero-caption p{font-family:"Roboto Condensed",Arial,sans-serif;font-weight:700;font-size:18px;line-height:18px;color:#3a2206;margin-top:12px}
.dots{position:absolute;left:348px;top:272px;display:flex;gap:3px}
.dots i{width:12px;height:12px;border-radius:50%;background:#2a1a06;border:1px solid #6b4a1a}
.dots i.on{background:#d9b26c;box-shadow:inset 0 0 0 3px #2a1a06}
.rule-dash{left:10px;top:398px;width:739px;border-top:2px dashed #dadada}

/* side column */
.side{left:-6px;top:436px;width:194px;box-shadow:0 0 10px rgba(0,0,0,.25)}
.side h2,.news h2,.main h2{font-family:"Roboto Condensed",Arial,sans-serif;font-weight:700;color:var(--ink)}
.side h2{font-size:22px;line-height:24px}
.contact{background:var(--contact);height:164px;padding:10px 16px;color:#fff;font-size:10px;line-height:13px}
.contact h2{color:var(--ink);margin-bottom:4px}
.contact .org{font-weight:700;font-size:12px;line-height:14px;margin-bottom:2px}
.contact .tel{margin-top:8px}
.contact b{font-weight:700}
.testi{background:var(--testi);height:173px;padding:10px 16px;font-size:10px;line-height:13px;color:var(--ink)}
.testi h2{margin-bottom:8px}
.testi .who{color:#7a5212;font-size:11px;line-height:12px;margin-top:6px}
.quote{background:var(--quote);height:172px;padding:10px 14px}
.quote h2{color:var(--testi);margin-bottom:8px}
.field{display:block;width:166px;height:22px;background:#fff;border-radius:3px;margin-bottom:3px;font-size:12px;line-height:22px;padding:0 6px;color:#222}
.submit{display:inline-block;margin-top:6px;background:var(--submit);color:var(--ink);font-family:"Roboto Condensed",Arial,sans-serif;font-weight:700;font-size:16px;line-height:22px;padding:0 4px;border-radius:3px}

/* main column */
.main h2{font-size:22px;line-height:26px}
.welcome{left:217px;top:430px}
.intro{left:219px;top:466px;width:510px;font-size:13.5px;line-height:16px;color:var(--ink);font-weight:700;opacity:.9}
.lead{left:219px;top:507px;width:362px;font-size:11.5px;line-height:15.4px}
.photo{background:linear-gradient(135deg,#dfe6ee,#7f8a96 60%,#3b3f46)}
.ph-welcome{left:607px;top:509px;width:126px;height:108px}
.story h2{font-size:20px}
.story-a{left:217px;top:652px}
.story-b{left:217px;top:817px}
.ph-story{width:104px;height:92px;border-radius:3px;background:linear-gradient(135deg,#c8d6e6,#8aa0bb 55%,#4a5a70)}
.ph-a{left:218px;top:682px}
.ph-b{left:218px;top:846px;background:linear-gradient(135deg,#f0ece6,#bfb4a6 55%,#6f6356)}
.story-text{width:212px;font-size:11.5px;line-height:15.4px}
.txt-a{left:338px;top:680px}
.txt-b{left:338px;top:844px}
.more{color:var(--gold-link);font-size:12px}
.divider{left:217px;top:799px;width:350px;border-top:1px solid #cfcfcf}

/* news */
.news{left:566px;top:659px;width:194px;height:278px;background:var(--news);padding:10px 16px;box-shadow:0 0 10px rgba(0,0,0,.25)}
.news h2{font-size:22px;line-height:24px;margin-bottom:6px}
.news-item{font-size:10px;line-height:13px;color:#fff;padding:6px 0 8px;border-bottom:1px solid rgba(60,30,0,.5)}
.news-item:last-child{border-bottom:0}
.news-item b{display:block;color:var(--ink);font-size:10.5px}
.news-item a{color:var(--ink);text-decoration:none}

/* partners */
.partners{left:0;top:988px;width:760px;height:82px;background:var(--band);display:flex;justify-content:center;align-items:center;gap:36px}
.partners span{display:block;background:var(--logo-grey);opacity:.85}

/* footer */
.footer-nav{position:absolute;left:0;width:912px;top:1140px;text-align:center;font-size:10.5px;color:#2b1c07}
.footer-nav a{color:#2b1c07;text-decoration:none}
.footer-nav .sep{margin:0 5px}
.copy{position:absolute;left:0;width:912px;top:1161px;text-align:center;font-size:10px;color:#2b1c07}
</style>
</head>
<body>
<div class="page">
  <div class="abs brand">
    <span class="brand-mark"></span>
    <span class="brand-name">Veltrane Information System</span>
  </div>
  <nav class="abs nav">
    <a class="active">Home</a><a>Solution</a><a>Hardware</a><a>Services</a><a>Clients</a><a>About Us</a><a>Contact Us</a>
  </nav>

  <section class="abs hero">
    <div class="hero-art" role="img" aria-label="Business team in silhouette around a meeting table with a globe behind, golden light"></div>
    <div class="hero-caption">
      <h1>Accounting software, networking,</h1>
      <p>hardware maintenance and consulting assistance</p>
    </div>
    <div class="dots"><i></i><i class="on"></i><i></i><i></i></div>
  </section>
  <div class="abs rule-dash"></div>

  <aside class="abs side">
    <div class="contact">
      <h2>Contact Us</h2>
      <p class="org">Veltrane Information System Pte Ltd</p>
      <p>18 Kessing Road<br># 03-21/22 Harrow Point<br>Singapore - 418265</p>
      <p class="tel"><b>Telephone No:</b> (065) 6471 - 5182<br><b>Facsimile No:</b> (065) 6471 - 5189</p>
    </div>
    <div class="testi">
      <h2>Testimonials</h2>
      <p>" The [staff at]...Veltrane Information Systems, are friendly attentive and supportive. Any problem, regardless of the time of day, ... "</p>
      <p class="who">-Group Data &amp; System Manager, Orlimax Technologies Ltd</p>
      <p>(Article featured in IT Hub Asia magazine, Oct 2000)</p>
    </div>
    <div class="quote">
      <h2>Request A Quote</h2>
      <span class="field">Name</span>
      <span class="field">Email</span>
      <span class="field">Mobile</span>
      <span class="submit">Submit</span>
    </div>
  </aside>

  <div class="main">
    <h2 class="abs welcome">Welcome to Veltrane Information System</h2>
    <p class="abs intro">Lorem ipsum dolor sit amet, consectetur adipiscing elit. Sed id tempus enim. Etiam eros velit, rutrum in fringilla id, fermentum sit amet nulla. Nullam cursus mi ut</p>
    <p class="abs lead">Aenean dapibus lorem laoreet ante pharetra ornare malesuada orci ornare. Ut volutpat ipsum ipsum, eget suscipit mauris. Sed sed nisl ac justo rutrum convallis. Fusce facilisis, nunc et viverra iaculis, arcu augue tempor ipsum, ut auctor sapien justo ac metus. Morbi adipiscing sodales condimentum. Nunc porta hendrerit turpis, nec pharetra enim interdum id. Aenean dapibus lorem laoreet ante pharetra ornare malesuada orci ornare. Ut volutpat ipsum ipsum, eget suscipit mauris.</p>
    <div class="abs photo ph-welcome" role="img" aria-label="Business people in a meeting room"></div>

    <div class="story">
      <h2 class="abs story-a">Success Stories</h2>
      <div class="abs ph-story ph-a" role="img" aria-label="Office team working at a laptop"></div>
      <p class="abs story-text txt-a">Sed lacinia vulputate dolor, nec congue nunc accumsan at. Praesent leo magna, imperdiet et mollis sed, hendrerit id nunc. Vestibulum et dolor enim. Cum sociis natoque penatibus et magnis dis<br><span class="more">Read More</span></p>
      <div class="abs divider"></div>
      <h2 class="abs story-b">Latest Korvin</h2>
      <div class="abs ph-story ph-b" role="img" aria-label="Audience applauding at a business event"></div>
      <p class="abs story-text txt-b">Sed lacinia vulputate dolor, nec congue nunc accumsan at. Praesent leo magna, imperdiet et mollis sed, hendrerit id nunc. Vestibulum et dolor enim. Cum sociis natoque penatibus et magnis dis<br><span class="more">Read More</span></p>
    </div>
  </div>

  <aside class="abs news">
    <h2>Recent News</h2>
    <div class="news-item"><b>Nam quis ligula a nibh fermentum venenatis vitae</b>Sed lacinia vulputate dolor, nec congue nunc accumsan at. Praesent leo magna... <a>read more</a></div>
    <div class="news-item"><b>Aenean dapibus lorem laoreet ante pharetra ornare</b>Ut volutpat ipsum ipsum, eget suscipit mauris. Sed sed nisl ac justo rutrum convallis... <a>read more</a></div>
    <div class="news-item"><b>Aenean dapibus lorem laoreet ante pharetra ornare</b>Ut volutpat ipsum ipsum, eget suscipit mauris. Sed sed nisl ac justo rutrum convallis... <a>read more</a></div>
  </aside>

  <div class="abs partners" aria-label="Partner badges">
    <span style="width:72px;height:26px;border-radius:4px"></span>
    <span style="width:98px;height:24px;border-radius:4px"></span>
    <span style="width:46px;height:46px;border-radius:50%"></span>
    <span style="width:52px;height:46px;border-radius:4px"></span>
    <span style="width:104px;height:28px;border-radius:4px"></span>
  </div>
</div>

<nav class="footer-nav">
  <a>Home</a><span class="sep">•</span><a>Solution</a><span class="sep">•</span><a>Hardware</a><span class="sep">•</span><a>Services</a><span class="sep">•</span><a>Clients</a><span class="sep">•</span><a>About Us</a><span class="sep">•</span><a>Contact Us</a>
</nav>
<p class="copy">© Copyright 2013. All Rights Reserved.</p>
</body>
</html>
```